Business Card Design Project

I need a business card designed from scratch. I have an existing logo that I can upload in Illustrator for modification or redesign.

The Company is called Query Lanterns http://querylanterns.com.au and we provide Search Engine Optimization services to Australian businesses. The current logo signifies an increase in visitors, profits etc...

There are no restrictions as to the redesign - colours, style etc are all open to change.

Cards will be full colour and one sided printed at http://www.cardmoxel.com.au so check their requirements for file format and sizes etc.

I will expect all original files upon completion of project.

Target Market(s)

Any business with a web site looking to improve their search engine rankings

Industry/Entity Type

Business

Requirements
Must have
• I like modern, sleek designs. Clean, not fussy, uncluttered.

```html
<!DOCTYPE html>
<html lang="en">
<head>
<meta charset="utf-8">
<title>Query Lanterns – Business Card</title>
<link rel="stylesheet" href="https://fonts.googleapis.com/css2?family=PT+Sans:wght@400;700&display=swap">
<style>
  :root {
    --stage: #4a2f1e;
    --white: #ffffff;
    --blue-light: #2f8fd6;
    --blue-mid: #2070b8;
    --blue-deep: #1c4a86;
    --brand-blue: #1f74bd;
    --accent-yellow: #f5c21a;
    --text-light: #ffffff;
  }
  * { box-sizing: border-box; margin: 0; padding: 0; }
  html, body {
    width: 1200px; height: 412px; overflow: hidden;
    background: var(--stage);
    font-family: "PT Sans", "Helvetica Neue", Arial, sans-serif;
  }
  .canvas { position: relative; width: 1200px; height: 412px; }
  .card {
    position: absolute; top: 64px;
    width: 498px; height: 284px; overflow: hidden;
  }
  .card-front { left: 72px; background: var(--white); }
  .card-back {
    left: 632px;
    background: radial-gradient(ellipse at 40% 42%, var(--blue-light) 0%, var(--blue-mid) 40%, var(--blue-deep) 100%);
  }
  .front-wave { position: absolute; inset: 0; }
  .brand {
    position: absolute; left: 22px; top: 124px;
    display: flex; align-items: center; gap: 8px;
  }
  .brand-dot {
    width: 14px; height: 14px; border-radius: 50%;
    background: var(--accent-yellow);
  }
  .brand-name {
    font-weight: 700; font-size: 28px; line-height: 1;
    color: var(--brand-blue); letter-spacing: -0.5px;
  }
  .contact {
    position: absolute; left: 306px; top: 76px;
    color: var(--text-light);
  }
  .person { font-size: 16px; font-weight: 700; margin-bottom: 14px; }
  .person .role { font-weight: 400; font-size: 13px; }
  .contact-list { list-style: none; font-size: 12px; line-height: 17px; }
  .contact-list li { display: flex; align-items: center; gap: 6px; }
  .contact-list svg { width: 9px; height: 9px; flex: none; fill: var(--text-light); }
  .address { margin-top: 9px; font-size: 13px; line-height: 17px; }
  .back-name {
    position: absolute; left: 0; right: 0; top: 100px;
    text-align: center; font-size: 38px; font-weight: 700;
    color: var(--accent-yellow); letter-spacing: -0.5px;
  }
  .back-url {
    position: absolute; left: 0; right: 0; top: 236px;
    text-align: center; font-size: 12px; font-weight: 700;
    color: var(--text-light); letter-spacing: 4.6px;
  }
</style>
</head>
<body>
<main class="canvas">
  <section class="card card-front">
    <svg class="front-wave" viewBox="0 0 498 284" preserveAspectRatio="none" aria-hidden="true">
      <defs>
        <linearGradient id="panelGradient" x1="0" y1="0" x2="1" y2="0.3">
          <stop offset="0" stop-color="#2c8ad0"/>
          <stop offset="1" stop-color="#1c4a86"/>
        </linearGradient>
      </defs>
      <path d="M278 0 C298 50 292 120 276 170 C262 215 252 250 260 284 L498 284 L498 0 Z" fill="url(#panelGradient)"/>
      <path d="M270 0 C290 50 284 120 268 170 C254 215 244 250 252 284" fill="none" stroke="#1f74bd" stroke-width="3"/>
    </svg>
    <div class="brand">
      <span class="brand-dot"></span>
      <span class="brand-name">Query Lanterns</span>
    </div>
    <div class="contact">
      <p class="person">Your Name / <span class="role">Title</span></p>
      <ul class="contact-list">
        <li><svg viewBox="0 0 10 10"><path d="M2 0.5 L4 2.5 L3 3.7 C3.6 5 5 6.4 6.3 7 L7.5 6 L9.5 8 L8 9.5 C4 9 1 6 0.5 2 Z"/></svg>098 765 4321</li>
        <li><svg viewBox="0 0 10 10"><rect x="2.5" y="0" width="5" height="10" rx="1"/><rect x="3.5" y="1.5" width="3" height="5" fill="#1f6cb0"/></svg>098 765 4321</li>
        <li><svg viewBox="0 0 10 10"><rect x="0" y="2" width="10" height="7" rx="1"/><path d="M0.5 2.5 L5 6 L9.5 2.5" fill="none" stroke="#1f6cb0" stroke-width="1"/></svg>enquiry@querylanterns.com.au</li>
        <li><svg viewBox="0 0 10 10"><circle cx="5" cy="5" r="4.8"/><path d="M0.5 5 H9.5 M5 0.5 V9.5" stroke="#1f6cb0" stroke-width="0.8"/></svg>www.querylanterns.com.au</li>
      </ul>
      <p class="address">Complex name,Street name<br>City, State, zip code</p>
    </div>
  </section>

  <section class="card card-back">
    <p class="back-name">Query Lanterns</p>
    <p class="back-url">www.querylanterns.com.au</p>
  </section>
</main>
</body>
</html>
```